Brivora Distance Learning Website

Brivora provide e-learning and mixed learning solutions for individuals, colleges, organisations and B2B.
We need a modern, light and flat website design for Brivora. We want to to see the designer incorporate user experience(UX) design elements into the AI or PSD mockups. We would like to see designs that use pastel colors that compliment yellow and black of our logo.
We want our E-learning experience to accelerate learning and for the interface to be user friendly and intuitive. We want the designs to focus on quick access to course information, course reviews, learning progress and study advice. Quick and intuitive access to all content for our clients is one of our top priorities.
We would like designs for the following project 3 pages:
1. Learner homepage dashboard (see attached screenshot).
On this page the Learners need to:
- Login
- Have quick access to Packages and Courses.
- See other recommended courses (Below Packages and Courses)
- Possibly a left hand side column/menu with thumbnail icons (See lumeqa learner dashboard screenshot)
2. Homepage
See current sample
http://www.brivora-learn.example
We would like the designer to focus on creating a customized banner to enhance the home page.
3. Primary Landing/Marketing page
This page is geared towards customer acquisition with the focal point being the top banner (video or HD image).
And Course Preview content below.
See reference
http://brivora-learn.example/subscriptionPlans/marketing/MTc%3D/Mjc4Nw%3D%3D/Speaking%20Nepali%20%2B%20Nepali%20Snacks%20Bundle%20by%20Lorne%20Pike%20Vell
Other site we like:
- https://www.skillorva.example (We like the home page and top bar on courses page)
- http://www.tutorcrest.example
- http://pixelgrovelab.example (think this site looks great, love the lower graphics on the homepage)
Updates
Hello,
Thank you for taking the time to contribute to this web design competition. We would just like to point out a few things:
1. Please try to make the color palette similar to the colors used in the screenshot that we just uploaded ('possible color palette).
2. Please make the designs specific to each page: THE LEARNER HOMEPAGE, HOME PAGE, and the MARKETING LANDING PAGE.
We are very happy with the high quality of designs so far,
Cheers,
Ned Ru
VK-Studio
Also,
Please avoid using dark/bold elements in the designs. The ONLY elements that we want to be dark are the logo and the footer.
Any questions please ask,
Cheers,
Ned Ru
Vk-Studio
Hello,
Based on the round of feedback we just gave it would be great if you could complete further design changes by tomorrow, as we are pushed for time.
Thank you,
Ned Ru
VK-Studio

```html
<!DOCTYPE html>
<html lang="en">
<head>
<meta charset="utf-8">
<title>Brivora – E-learning and mixed learning solutions</title>
<link rel="stylesheet" href="https://fonts.googleapis.com/css2?family=Raleway:wght@400;500;600;700&family=Open+Sans:wght@400;600;700&display=swap">
<style>
:root{
  --blue:#1d6ea6;
  --blue-deep:#0f4e7c;
  --navy:#0b3a5c;
  --sidebar:#0d466f;
  --orange:#f7a11a;
  --amber:#f0a600;
  --amber-light:#f9c230;
  --title-blue:#1d6a9c;
  --ink:#333;
  --muted:#666;
  --footer:#1b1b1b;
  --white:#fff;
}
*{box-sizing:border-box;margin:0;padding:0}
html,body{width:770px;height:1200px;overflow:hidden;background:#fff}
body{position:relative;font-family:"Open Sans",Arial,sans-serif;color:var(--ink)}
.abs{position:absolute}

/* header */
.site-header{left:0;top:0;width:770px;height:60px;background:#fff}
.brand{left:101px;top:15px;display:flex;align-items:center;gap:6px;font-family:"Raleway",sans-serif;font-size:25px;font-weight:500;color:var(--title-blue)}
.brand-mark{width:10px;height:10px;background:var(--orange)}
.login-form{left:426px;top:26px;display:flex;align-items:center}
.field{width:103px;height:16px;border:2px solid #ddd;border-radius:9px;font-size:6.5px;color:#888;padding:2px 8px;background:#fafafa;margin-right:6px}
.field.pw{width:100px;margin-right:0;border-radius:9px 0 0 9px}
.login-btn{width:40px;height:16px;margin-left:-6px;border-radius:9px;background:var(--orange);color:#fff;font-size:7px;font-weight:700;display:flex;align-items:center;justify-content:center}

/* hero */
.hero{left:0;top:60px;width:704px;height:299px;background:linear-gradient(90deg,#0f5b8f 0%,#186fa6 40%,#2b7fb4 60%,#6a9cc0 100%)}
.hero-photo{left:320px;top:60px;width:384px;height:299px;background:linear-gradient(100deg,rgba(24,111,166,0) 0%,rgba(150,170,185,.55) 35%,#c9c7c3 65%,#b7b2ac 100%)}
.hero-kicker{left:99px;top:138px;font-family:"Raleway",sans-serif;font-size:20px;color:var(--orange);font-weight:500}
.hero-title{left:99px;top:162px;font-family:"Raleway",sans-serif;font-size:28px;color:#fff;font-weight:500}
.hero-text{left:101px;top:199px;width:210px;font-size:7.6px;line-height:1.5;color:#e8f1f8}
.btn{display:flex;align-items:center;justify-content:center;font-size:7.5px;font-weight:600}
.btn-try{left:101px;top:234px;width:73px;height:19px;background:var(--orange);color:#fff}
.btn-more{left:178px;top:234px;width:72px;height:19px;background:#fff;color:#333}
.dots{left:102px;top:261px;display:flex;gap:3px}
.dots span{width:8px;height:8px;border-radius:50%;background:#7fa9c9}
.dots span:first-child{background:#fff}

.side-nav{left:704px;top:60px;width:66px;height:299px;background:var(--sidebar)}
.side-nav a{position:absolute;left:0;width:66px;text-align:center;color:#fff;text-decoration:none;font-size:8.5px}
.side-nav svg{display:block;margin:0 auto 2px}

/* feature band */
.features{left:0;top:359px;width:770px;height:63px;background:var(--blue)}
.feature{top:14px;width:190px;color:#fff}
.feature h3{font-family:"Raleway",sans-serif;font-size:10.5px;font-weight:600;letter-spacing:.2px;margin-bottom:3px}
.feature p{font-size:6.5px;line-height:1.75;color:#d6e6f2}
.divider{top:0;width:1px;height:63px;background:#4f8fbd}

/* cards */
.card{top:449px;width:178px;text-align:center}
.card-img{width:178px;height:87px}
.card h2{font-family:"Raleway",sans-serif;font-size:12.5px;font-weight:500;color:var(--title-blue);margin-top:9px}
.card p{font-size:6.6px;line-height:1.8;color:var(--muted);margin-top:4px}
.card .read{display:inline-flex;margin-top:6px;width:60px;height:16px;background:var(--blue-deep);color:#fff;font-size:7px;font-weight:600;align-items:center;justify-content:center}

/* packages */
.packages{left:0;top:651px;width:770px;height:255px;background:var(--amber)}
.pk-title{left:101px;top:692px;font-family:"Raleway",sans-serif;font-size:21px;color:#fff;font-weight:500}
.pk-text{left:102px;top:722px;width:258px;font-size:6.5px;line-height:1.8;color:#fde8b8}
.pk-text p+p{margin-top:4px}
.pk-box{top:790px;width:86px;height:74px;color:#fff;text-align:center;padding-top:13px}
.pk-box h4{font-family:"Raleway",sans-serif;font-size:8.5px;font-weight:700;margin-top:3px}
.pk-box p{font-size:5.3px;line-height:1.5;margin-top:1px;padding:0 8px}
.pk-ind{left:102px;background:#1b6fae}
.pk-col{left:190px;background:var(--navy)}
.pk-bus{left:278px;background:var(--amber-light)}
.pk-bus p{color:#fff3cf}
.pk-art{left:416px;top:680px;width:224px;height:202px;border-radius:4px;background:linear-gradient(160deg,#d9dde2 0%,#b9c3cc 60%,#e8b480 100%);opacity:.9}

/* recommended */
.rec-title{left:0;top:943px;width:770px;text-align:center;font-family:"Raleway",sans-serif;font-size:16px;font-weight:400;color:#444}
.rec{top:985px;width:136px;text-align:center}
.rec-img{width:136px;height:65px}
.rec h5{font-family:"Raleway",sans-serif;font-size:9px;font-weight:600;color:#333;margin-top:14px}
.rec p{font-size:6.5px;line-height:1.55;color:var(--muted);margin-top:2px}

/* footer */
.site-footer{left:0;top:1138px;width:770px;height:62px;background:var(--footer)}
.foot-nav{left:102px;top:1156px;font-size:7.8px;font-weight:600;color:#fff}
.foot-nav span{color:#bbb;margin:0 4px}
.copy{left:102px;top:1173px;font-size:6.5px;color:#bbb}
.social{left:612px;top:1154px;display:flex;gap:4px}
.social span{width:14px;height:14px;border-radius:3px;background:#fff}
</style>
</head>
<body>

<header class="site-header abs">
  <div class="brand abs"><span class="brand-mark"></span>Brivora</div>
  <form class="login-form abs">
    <div class="field">Username</div>
    <div class="field pw">Password</div>
    <div class="login-btn">Login</div>
  </form>
</header>

<section class="hero abs"></section>
<div class="hero-photo abs" role="img" aria-label="Photo of a young woman on a sofa studying on a laptop"></div>
<div class="hero-kicker abs">E-learning and mixed</div>
<h1 class="hero-title abs">Learning solutions</h1>
<p class="hero-text abs">Morbi ornare gravida elit Integer congue augue et male-suada iaculis ipsum dui aliquet felis at cursus</p>
<div class="btn btn-try abs">TRY IT NOW</div>
<div class="btn btn-more abs">READ MORE</div>
<div class="dots abs"><span></span><span></span><span></span></div>

<nav class="side-nav abs">
  <a style="top:30px"><svg width="16" height="16" viewBox="0 0 16 16"><circle cx="8" cy="8" r="7.5" fill="#fff"/><text x="8" y="12" font-size="11" font-weight="700" text-anchor="middle" fill="#0d466f" font-family="Arial">?</text></svg>About</a>
  <a style="top:72px"><svg width="18" height="15" viewBox="0 0 18 15"><rect x="1" y="1" width="16" height="10" fill="none" stroke="#fff" stroke-width="2"/><rect x="7" y="11" width="4" height="2" fill="#fff"/><rect x="4" y="13" width="10" height="2" fill="#fff"/></svg>Courses</a>
  <a style="top:116px"><svg width="18" height="15" viewBox="0 0 18 15"><rect x="6" y="0.8" width="6" height="3" fill="none" stroke="#fff" stroke-width="1.6"/><rect x="1" y="4" width="16" height="10" rx="1" fill="#fff"/><rect x="1" y="8" width="16" height="1" fill="#0d466f"/></svg>Packags</a>
  <a style="top:160px"><svg width="18" height="14" viewBox="0 0 18 14"><rect x="1" y="1" width="16" height="11" fill="none" stroke="#fff" stroke-width="2"/><circle cx="9" cy="6.5" r="3" fill="#fff"/></svg>Buy Now</a>
  <a style="top:204px"><svg width="16" height="16" viewBox="0 0 16 16"><path d="M2 14 L9 7" stroke="#fff" stroke-width="3" stroke-linecap="round"/><circle cx="11" cy="5" r="4" fill="#fff"/><circle cx="12.5" cy="3.5" r="1.6" fill="#0d466f"/></svg>Support</a>
  <a style="top:246px"><svg width="16" height="15" viewBox="0 0 16 15"><path d="M3 1 L6 1 L7 4 L5 6 Q7 9 10 10 L12 8 L15 9 L15 12 Q14 14 12 14 Q3 12 1 3 Q1 1 3 1Z" fill="#fff"/></svg>Contact</a>
</nav>

<section class="features abs">
  <div class="feature abs" style="left:105px"><h3>VIVAMUS PORTTITOR</h3><p>Morbi ornare gravida elit Integer congue augue et malesi-aculis ipsum dui aliquet felis at cursus magna</p></div>
  <div class="divider abs" style="left:288px"></div>
  <div class="feature abs" style="left:305px"><h3>MAURIS VEL LACUS</h3><p>Morbi ornare gravida elit Integer congue augue et malesi-aculis ipsum dui aliquet felis at cursus magna</p></div>
  <div class="divider abs" style="left:484px"></div>
  <div class="feature abs" style="left:498px"><h3>CUM SOCIIS NATOQUE</h3><p>Morbi ornare gravida elit Integer congue augue et malesi-aculis ipsum dui aliquet felis at cursus magna</p></div>
</section>

<article class="card abs" style="left:98px">
  <div class="card-img" role="img" aria-label="Photo of a hand touching glowing gears labelled learn and lead" style="background:linear-gradient(135deg,#1a2533 0%,#2f4f6e 50%,#14202c 100%)"></div>
  <h2>Why We Are</h2>
  <p>Morbi ornare gravida elit Integer congue augue et malesuada iaculis ipsum dui aliquet felis at cursus magna nisl nec elit Praesent elementum elit at tellus nec ultricie</p>
  <span class="read">Read More</span>
</article>
<article class="card abs" style="left:295px">
  <div class="card-img" role="img" aria-label="Image of an open book with glowing e-learning text above it" style="background:linear-gradient(180deg,#0c3a7a,#1e6cc0 60%,#0a2d5e)"></div>
  <h2>Our Courses</h2>
  <p>Morbi ornare gravida elit Integer congue augue et malesuada iaculis ipsum dui aliquet felis at cursus magna nisl nec elit Praesent elementum elit at tellus nec ultricie</p>
  <span class="read">Read More</span>
</article>
<article class="card abs" style="left:493px">
  <div class="card-img" role="img" aria-label="Photo of a group of students studying together" style="background:linear-gradient(135deg,#c9b9a6,#a98a74 50%,#7a8a8a)"></div>
  <h2>Join Us Now</h2>
  <p>Morbi ornare gravida elit Integer congue augue et malesuada iaculis ipsum dui aliquet felis at cursus magna nisl nec elit Praesent elementum elit at tellus nec ultricie</p>
  <span class="read">Read More</span>
</article>

<section class="packages abs"></section>
<h2 class="pk-title abs">Our Packages</h2>
<div class="pk-text abs">
  <p>Morbi diam mauris viverra in gravida eu mattis in ante Morbi eget arcu Morbi porta libero id ullamcorper nonummy nibh ligula pulvinar metus eget consectetuer augue nisi quis lacus Ut ac mi quis lacus mollis aliquam</p>
  <p>Class aptent taciti sociosqu ad litora torquent per conubia nostra per inceptos hyme-naeos Proin nulla arcu nonummy luctus dictum eget</p>
</div>
<div class="pk-box pk-ind abs">
  <svg width="16" height="18" viewBox="0 0 16 18"><circle cx="8" cy="5" r="4.5" fill="#fff"/><path d="M0 18 Q0 10 8 10 Q16 10 16 18Z" fill="#fff"/></svg>
  <h4>INDIVIDUAL</h4><p>Mauris vel lacus vitae felis vestibulum volutpat</p>
</div>
<div class="pk-box pk-col abs">
  <svg width="24" height="18" viewBox="0 0 24 18"><circle cx="5" cy="5" r="3" fill="#fff"/><circle cx="19" cy="5" r="3" fill="#fff"/><circle cx="12" cy="4" r="4" fill="#fff"/><path d="M0 15 Q0 9 5 9 Q10 9 10 15Z M14 15 Q14 9 19 9 Q24 9 24 15Z" fill="#fff"/><path d="M5 18 Q5 9 12 9 Q19 9 19 18Z" fill="#fff"/></svg>
  <h4>COLLEGE</h4><p>Mauris vel lacus vitae felis vestibulum volutpat</p>
</div>
<div class="pk-box pk-bus abs">
  <svg width="22" height="18" viewBox="0 0 22 18"><rect x="7" y="1" width="8" height="4" fill="none" stroke="#fff" stroke-width="1.8"/><rect x="1" y="5" width="20" height="13" rx="1" fill="#fff"/><rect x="1" y="10" width="20" height="1.2" fill="#f9c230"/></svg>
  <h4>BUSINESS</h4><p>Mauris vel lacus vitae felis vestibulum volutpat</p>
</div>
<div class="pk-art abs" role="img" aria-label="Flat illustration of hands typing on a laptop beside a clipboard and an envelope"></div>

<h2 class="rec-title abs">Other Recommended Courses</h2>
<article class="rec abs" style="left:97px">
  <div class="rec-img" role="img" aria-label="Image of laptops arranged in a circle around a graduation cap" style="background:linear-gradient(180deg,#f3f3f3,#d8d8d8)"></div>
  <h5>Morbi ornare gravida</h5><p>Morbi ornare gravida elit Integer congue augue et malesuada iaculis ipsum dui aliquet felis at cursus magna</p>
</article>
<article class="rec abs" style="left:242px">
  <div class="rec-img" role="img" aria-label="Image of a blue arrow reading e-learning" style="background:linear-gradient(135deg,#3d8fd8,#1f63b0)"></div>
  <h5>Curabitur iaculis</h5><p>Morbi ornare gravida elit Integer congue augue et malesuada iaculis ipsum dui aliquet felis at cursus magna</p>
</article>
<article class="rec abs" style="left:388px">
  <div class="rec-img" role="img" aria-label="Photo of a woman working on a laptop" style="background:linear-gradient(135deg,#8e8a84,#d9d6d1)"></div>
  <h5>Luctus dictum eget</h5><p>Morbi ornare gravida elit Integer congue augue et malesuada iaculis ipsum dui aliquet felis at cursus magna</p>
</article>
<article class="rec abs" style="left:534px">
  <div class="rec-img" role="img" aria-label="Image of an open book under glowing digital light" style="background:linear-gradient(180deg,#0d3c78,#2a78c8 60%,#0a2c5a)"></div>
  <h5>Nunc porta convallis</h5><p>Morbi ornare gravida elit Integer congue augue et malesuada iaculis ipsum dui aliquet felis at cursus magna</p>
</article>

<footer class="site-footer abs"></footer>
<nav class="foot-nav abs">About<span>|</span>Courses<span>|</span>Packages<span>|</span>Buy Now<span>|</span>Support<span>|</span>Contact</nav>
<p class="copy abs">© 2015 Company Name &nbsp;All right reserved &nbsp;Term of Use</p>
<div class="social abs" aria-label="Social links"><span></span><span></span><span></span></div>

</body>
</html>
```